New Business Card for Web Design/Internet Marketing Company

Looking for a great looking new business card. We are a 10 year old web design, internet marketing and website management company that works mostly with small businesses.

Our new card needs to better match the colors and style of our website, be bold, extremely usable and slightly edgy.

Target Market(s)

Small/Medium businesses that have websites

Industry/Entity Type

Internet

Requirements
Must have
• Front and back design, full color, rounded corners please

Must use the colors/style of our website (JPG provided)

INFO FOR CARDS (as readable as possible please)
Mark Lenner
President/CEO
mark@trelvanmedia.example
Phone: 520-381-7459
Toll Free: 866-381-7459
Address: 4315 W. Calloway Ave. Ste. 140, Tucson, AZ 85792

THINGS I WANT TO PROMOTE (if there is room):
1. Our Website - www.trelvanmedia.example

2. Social Media
Twitter: @trelvanmedia
Facebook: www.facebook.com/trelvanmedia

3. Our Services
Web Design
Internet Marketing
Website Management

```html
<!DOCTYPE html>
<html lang="en">
<head>
<meta charset="utf-8">
<title>Trelvan Media business card</title>
<link rel="stylesheet" href="https://fonts.googleapis.com/css2?family=Source+Sans+3:wght@400;600;700&display=swap">
<style>
  :root {
    --stage: #e8e3db;
    --navy: #0f1b30;
    --navy-faint: #2a3950;
    --orange: #f08a2c;
    --accent-rule: #b5693a;
    --white: #ffffff;
    --text-soft: #d9dee6;
    --divider: #8a94a3;
  }
  * { margin: 0; padding: 0; box-sizing: border-box; }
  html, body {
    width: 1200px; height: 1036px; overflow: hidden;
    background: var(--stage);
    font-family: "Source Sans 3", "Myriad Pro", sans-serif;
  }
  .card {
    position: absolute;
    width: 737px; height: 419px;
    background: var(--navy);
    border-radius: 28px;
    overflow: hidden;
    color: var(--white);
  }
  .card--front { left: 63px; top: 52px; }
  .card--back  { left: 371px; top: 544px; }

  /* front */
  .brand {
    position: absolute; left: 38px; top: 150px; width: 330px;
    text-align: center;
  }
  .brand__name {
    font-size: 46px; font-weight: 700; color: var(--orange);
    letter-spacing: -0.5px; line-height: 1;
  }
  .brand__tagline {
    margin-top: 10px;
    font-size: 17px; font-weight: 400; color: var(--divider);
  }
  .brand__dot {
    position: absolute; left: 140px; top: -92px;
    width: 52px; height: 52px; border-radius: 50%;
    background: var(--orange);
  }
  .divider {
    position: absolute; left: 396px; top: 88px;
    width: 2px; height: 194px;
    background: linear-gradient(to bottom, transparent, var(--divider) 20%, var(--divider) 80%, transparent);
  }
  .contact {
    position: absolute; left: 425px; top: 104px;
    list-style: none;
    font-size: 18px; color: var(--text-soft); line-height: 26px;
  }
  .contact__item { display: flex; align-items: center; gap: 9px; }
  .contact__icon { width: 15px; height: 15px; flex: none; }
  .address {
    position: absolute; left: 425px; top: 229px;
    font-size: 18px; line-height: 24px; color: var(--text-soft);
    font-style: normal;
  }
  .rule {
    position: absolute; left: 46px; top: 352px;
    width: 320px; height: 4px;
    background: var(--accent-rule);
  }
  .person {
    position: absolute; left: 46px; top: 370px;
    font-size: 20px; font-weight: 400;
  }
  .person__name { font-size: 26px; font-weight: 700; }

  /* back */
  .backdrop { position: absolute; left: 0; top: 0; }
  .services {
    position: absolute; left: 0; right: 0; top: 148px;
    list-style: none; text-align: center;
    font-size: 30px; font-weight: 700; line-height: 41px;
  }
  .services li::before {
    content: ""; display: inline-block;
    width: 10px; height: 10px; border-radius: 50%;
    background: var(--white); margin-right: 10px; vertical-align: middle;
    position: relative; top: -3px;
  }
  .social {
    position: absolute; left: 0; right: 0; top: 338px;
    display: flex; justify-content: center; gap: 22px;
    font-size: 25px; color: var(--text-soft);
  }
  .social__item { display: flex; align-items: center; gap: 10px; }
  .social__mark { width: 18px; height: 18px; background: var(--text-soft); border-radius: 3px; }
</style>
</head>
<body>

<section class="card card--front" aria-label="Card front">
  <div class="brand">
    <span class="brand__dot" aria-hidden="true"></span>
    <div class="brand__name">Trelvan Media</div>
    <div class="brand__tagline">Built to Perform</div>
  </div>

  <div class="divider" aria-hidden="true"></div>

  <ul class="contact">
    <li class="contact__item">
      <svg class="contact__icon" viewBox="0 0 16 16" aria-hidden="true"><circle cx="8" cy="8" r="7" fill="none" stroke="var(--orange)" stroke-width="1.6"/><path d="M5.5 4.5l1.5 1.7-1 1.2a5 5 0 0 0 2.6 2.6l1.2-1 1.7 1.5-1 1.4c-3 0-6.4-3.4-6.4-6.4z" fill="var(--orange)"/></svg>
      866-381-7459
    </li>
    <li class="contact__item">
      <svg class="contact__icon" viewBox="0 0 16 16" aria-hidden="true"><circle cx="8" cy="8" r="7" fill="none" stroke="var(--orange)" stroke-width="1.6"/><path d="M5.5 4.5l1.5 1.7-1 1.2a5 5 0 0 0 2.6 2.6l1.2-1 1.7 1.5-1 1.4c-3 0-6.4-3.4-6.4-6.4z" fill="var(--orange)"/></svg>
      520-381-7459
    </li>
    <li class="contact__item">
      <svg class="contact__icon" viewBox="0 0 16 16" aria-hidden="true"><rect x="1" y="3" width="14" height="10" rx="2" fill="var(--orange)"/><path d="M2 4.5l6 4.5 6-4.5" fill="none" stroke="var(--navy)" stroke-width="1.4"/></svg>
      mark@trelvanmedia.example
    </li>
    <li class="contact__item">
      <svg class="contact__icon" viewBox="0 0 16 16" aria-hidden="true"><circle cx="8" cy="8" r="7" fill="var(--orange)"/><path d="M1.5 6h13M1.5 10h13" stroke="var(--navy)" stroke-width="1.3"/></svg>
      www.trelvanmedia.example
    </li>
  </ul>

  <address class="address">
    4315 W. Calloway Ave. Ste. 140<br>
    Tucson, AZ 85792
  </address>

  <div class="rule" aria-hidden="true"></div>
  <p class="person"><span class="person__name">Mark Lenner ,</span> President/CEO</p>
</section>

<section class="card card--back" aria-label="Card back">
  <svg class="backdrop" width="737" height="419" viewBox="0 0 737 419" aria-hidden="true">
    <circle cx="360" cy="212" r="150" fill="var(--navy-faint)" opacity="0.55"/>
  </svg>

  <ul class="services">
    <li>Web Design</li>
    <li>Internet Marketing</li>
    <li>Website Management</li>
  </ul>

  <div class="social">
    <span class="social__item"><span class="social__mark" aria-hidden="true"></span>@trelvanmedia</span>
    <span class="social__item"><span class="social__mark" aria-hidden="true"></span>trelvanmedia</span>
  </div>
</section>

</body>
</html>
```